Creation of a construction/bricklaying business website

Following the template format of "Halloway 7", the following content would need to be included:
1. Landing page with 3 tiles that go to their own pages.
- Landing page to include background photo and description of services offered.
2. 3 tiles to include:
a) "Contact Us For A Free Quote or Friendly Discussion" Form (middle tile)
b) Case Studies and Testimonials
c) Certifications and Professional Membership
- Design logo to be used from previous SketchNestle project. Example of logo attached below, please access full JPG files from our account.

Target Market(s)

Prospective clients seeking construction work (bricklaying speciality)

Industry/Entity Type

Residential Construction

Coding

Coded - Design and coding required

Number of Pages Required

4 page

Font styles to use
Sans Serif

Colors

Designer to choose colors to be used in the design.

Requirements
Must have
• Following the template format of "Halloway 7", the following content would need to be included:
• 1. Landing parent page with 3 tiles that go to the 3 child pages.
• - Landing page to include background photo and description of services offered.
• 2. 3 tiles to include:
• a) "Contact Us For A Free Quote or Friendly Discussion" Form (middle tile)
• b) Case Studies and Testimonials (first tile / left side)
• c) Certifications and Professional Memberships (third tile / right side) (This should include logos of the relevant organisations being displayed. Specifically GQT and the Pillar Seal GQT).
• - Design logo to be used from previous SketchNestle project. Example of logo attached below, please access full JPG files from our account.
Nice to have
• Sleek and modern feel.
• Approachable in terms of how people can contact the company for a quote.
• Traditional pictures to give credibility and comfort around choosing this company.
Should not have
• Cheesy pictures
• Over-complicated
• Simple to use
• Easy URL domain name

```html
<!DOCTYPE html>
<html lang="en">
<head>
<meta charset="utf-8">
<title>R.T.Marsh Construction Ltd</title>
<link href="https://fonts.googleapis.com/css2?family=Exo+2:wght@500;600&family=Jost:wght@400;500&display=swap" rel="stylesheet">
<style>
:root{
  --blue:#1158a8;
  --footer-blue:#0d57a3;
  --ink:#1c1c1c;
  --white:#ffffff;
  --tile:#e9eceb;
  --grey-icon:#6d6d6d;
  --badge-red:#c8102e;
  --rule:rgba(255,255,255,.25);
}
*{margin:0;padding:0;box-sizing:border-box}
html,body{width:1034px;height:1200px;overflow:hidden;background:var(--white)}
body{font-family:"Jost",sans-serif;color:var(--ink);position:relative}
.hero{position:absolute;left:0;top:0;width:1034px;height:505px;
  background:linear-gradient(180deg,rgba(20,20,22,.55),rgba(20,20,22,.6)),
  linear-gradient(100deg,#4a2a22 0%,#6b3a2c 35%,#5a3a30 60%,#7a6a60 85%,#8c8a86 100%);}
.contact-top{position:absolute;top:18px;display:flex;align-items:center;gap:11px;color:var(--white);font-size:12.5px;line-height:19px}
.contact-top .dot{width:32px;height:32px;border-radius:50%;background:var(--blue);display:flex;align-items:center;justify-content:center}
.brand{font-family:"Exo 2",sans-serif;font-weight:600;color:var(--blue);text-align:center;position:absolute;left:0;width:100%}
.hero .brand{top:122px;font-size:42px}
.hero-title{position:absolute;top:235px;width:100%;text-align:center;font-family:"Exo 2",sans-serif;font-weight:600;color:var(--white);font-size:24px;line-height:28px}
.services{position:absolute;top:306px;width:100%;text-align:center;font-family:"Exo 2",sans-serif;font-weight:600;color:var(--white);font-size:17px;line-height:19px}
.services span{margin:0 14px}
.services span::before{content:"•";margin-right:14px}
.btn{position:absolute;left:447px;top:372px;width:139px;height:27px;background:var(--blue);color:var(--white);font-size:14px;display:flex;align-items:center;justify-content:center;gap:6px;text-decoration:none}
.intro .brand{top:552px;font-size:24px}
.intro-text{position:absolute;left:140px;width:754px;top:600px;text-align:center;font-size:13px;line-height:21px}
.intro-text p+p{margin-top:6px}
.tiles{position:absolute;left:140px;top:722px;display:flex}
.tile{width:251px;height:220px;text-align:center;padding-top:24px}
.tile.shaded{background:var(--tile)}
.tile .icon{height:54px;display:flex;justify-content:center;align-items:center;gap:4px}
.tile h3{font-family:"Exo 2",sans-serif;font-weight:600;font-size:12px;line-height:16px;margin-top:21px}
.tile p{font-size:11.5px;line-height:18.5px;margin-top:14px;padding:0 7px}
.badge{width:32px;height:53px;background:var(--badge-red)}
.footer{position:absolute;left:0;top:984px;width:1034px;height:216px;background:var(--footer-blue);color:var(--white)}
.footer .brand{color:var(--white);top:28px;font-size:22px}
.f-item{position:absolute;top:92px;display:flex;align-items:center;gap:10px;font-size:12px;line-height:19px}
.f-item .dot{width:32px;height:32px;border-radius:50%;background:var(--grey-icon);display:flex;align-items:center;justify-content:center}
.rule{position:absolute;left:164px;top:146px;width:696px;height:1px;background:var(--rule)}
.copyright{position:absolute;left:164px;top:170px;font-size:12px}
.social{position:absolute;left:745px;top:165px;display:flex;gap:4px}
.social span{width:26px;height:26px;border-radius:50%;background:var(--white)}
</style>
</head>
<body>
<section class="hero" role="img" aria-label="Photo of a newly built red brick garden wall along a residential street">
</section>
<div class="contact-top" style="left:140px">
  <span class="dot"><svg width="16" height="16" viewBox="0 0 24 24"><path fill="#fff" d="M6.6 10.8a15 15 0 0 0 6.6 6.6l2.2-2.2a1 1 0 0 1 1-.25 11.4 11.4 0 0 0 3.6.57 1 1 0 0 1 1 1V20a1 1 0 0 1-1 1A17 17 0 0 1 3 4a1 1 0 0 1 1-1h3.5a1 1 0 0 1 1 1c0 1.25.2 2.45.57 3.57a1 1 0 0 1-.25 1z"/></svg></span>
  <div>Call Us On :<br>123.456.7890</div>
</div>
<div class="contact-top" style="left:706px">
  <span class="dot"><svg width="17" height="12" viewBox="0 0 20 14"><rect x="1" y="1" width="18" height="12" fill="none" stroke="#fff" stroke-width="1.8"/><path d="M1 1l9 7 9-7" fill="none" stroke="#fff" stroke-width="1.8"/></svg></span>
  <div>Email<br>info@rtmarshconstruction.com</div>
</div>
<div class="brand">R.T.Marsh Construction Ltd</div>
<h1 class="hero-title">R.T.Marsh Construction Ltd is a construction company that<br>has expertise and experience in the following areas</h1>
<div class="services">
  <span>Extensions</span><span>New build / New houses</span><span>Garden walls</span><br>
  <span>Plastering</span><span>Brickwork</span><span>Groundworks</span>
</div>
<a class="btn" href="#">Contact Us Today <svg width="14" height="8" viewBox="0 0 14 8"><path d="M0 4h12M9 1l3 3-3 3" fill="none" stroke="#fff" stroke-width="1.2"/></svg></a>

<section class="intro">
  <div class="brand">R.T.Marsh Construction Ltd</div>
  <div class="intro-text">
    <p>We pride ourselves on attention to detail, pride in our completed project and client satisfaction. We believe in full transparency and this is reflected in the jobs we quote for you. We break down each step with both labour and materials cost so you can see exactly what you are paying for.</p>
    <p>Feel free to get in touch and we can talk through what you are looking to achieve.</p>
  </div>
</section>

<div class="tiles">
  <div class="tile shaded">
    <div class="icon">
      <svg width="80" height="54" viewBox="0 0 80 54"><rect x="34" y="1" width="42" height="52" rx="3" fill="#fff" stroke="#1f4f8f" stroke-width="2"/><rect x="38" y="6" width="24" height="5" fill="#9aa"/><path d="M40 18h30M40 24h22M40 30h18" stroke="#1158a8" stroke-width="2"/><circle cx="58" cy="34" r="7" fill="none" stroke="#1f4f8f" stroke-width="2.5"/><path d="M63 39l8 8" stroke="#1f4f8f" stroke-width="3"/><circle cx="30" cy="38" r="10" fill="#555"/><circle cx="18" cy="38" r="12" fill="#1158a8"/></svg>
    </div>
    <h3>Case Studies and<br>Testimonials</h3>
    <p>Ut wisi enim ad minim veniam, quis nostrud exerci tation ullamcorper suscipit lobortis nisl ut aliquip ex ea commodo consequat.</p>
  </div>
  <div class="tile">
    <div class="icon">
      <svg width="52" height="54" viewBox="0 0 52 54"><path d="M10 2h26l10 10v40H10z" fill="#fff" stroke="#1f4f8f" stroke-width="2.5"/><path d="M20 20h20M20 28h20M26 36h14" stroke="#1158a8" stroke-width="2"/><path d="M4 38l5 8 9-18" fill="none" stroke="#1f4f8f" stroke-width="3"/></svg>
    </div>
    <h3>Contact Us For A<br>Free Quote</h3>
    <p>Ut wisi enim ad minim veniam, quis nostrud exerci tation ullamcorper suscipit lobortis nisl ut aliquip ex ea commodo consequat.</p>
  </div>
  <div class="tile shaded">
    <div class="icon">
      <span class="badge" role="img" aria-label="Membership badge"></span>
      <span class="badge" role="img" aria-label="Pillar Seal GQT badge"></span>
    </div>
    <h3>Certifications and Professional<br>Memberships</h3>
    <p>Ut wisi enim ad minim veniam, quis nostrud exerci tation ullamcorper suscipit lobortis nisl ut aliquip ex ea commodo consequat.</p>
  </div>
</div>

<footer class="footer">
  <div class="brand">R.T.Marsh Construction Ltd</div>
  <div class="f-item" style="left:164px">
    <span class="dot"><svg width="12" height="16" viewBox="0 0 12 16"><path d="M6 0a6 6 0 0 1 6 6c0 4-6 10-6 10S0 10 0 6a6 6 0 0 1 6-6z" fill="#fff"/><circle cx="6" cy="6" r="2.2" fill="#6d6d6d"/></svg></span>
    <div>Street Name, City Name<br>State Zipcode</div>
  </div>
  <div class="f-item" style="left:442px">
    <span class="dot"><svg width="16" height="16" viewBox="0 0 24 24"><path fill="#fff" d="M6.6 10.8a15 15 0 0 0 6.6 6.6l2.2-2.2a1 1 0 0 1 1-.25 11.4 11.4 0 0 0 3.6.57 1 1 0 0 1 1 1V20a1 1 0 0 1-1 1A17 17 0 0 1 3 4a1 1 0 0 1 1-1h3.5a1 1 0 0 1 1 1c0 1.25.2 2.45.57 3.57a1 1 0 0 1-.25 1z"/></svg></span>
    <div>Call Us On :<br>123.456.7890</div>
  </div>
  <div class="f-item" style="left:670px">
    <span class="dot"><svg width="17" height="12" viewBox="0 0 20 14"><rect x="1" y="1" width="18" height="12" fill="none" stroke="#fff" stroke-width="1.8"/><path d="M1 1l9 7 9-7" fill="none" stroke="#fff" stroke-width="1.8"/></svg></span>
    <div>Email<br>info@rtmarshconstruction.com</div>
  </div>
  <div class="rule"></div>
  <div class="copyright">Copyright ©2018 R.T.Marsh Construction Ltd. All Rights Reserved.</div>
  <div class="social" aria-label="Social links"><span></span><span></span><span></span><span></span></div>
</footer>
</body>
</html>
```